FunBrixo Business Card

We need a business card design for our company. We sell construction-themed amusement rides for kids.

Contact Information for Business Card

Contact info on business card should include:
Carl Dunning
Co-Founder & COO
(833) 571-FUNBRIX
Carl@funbrixo-demo.com
www.funbrixo-demo.com

```html
<!DOCTYPE html>
<html lang="en">
<head>
<meta charset="utf-8">
<title>FunBrixo Business Card</title>
<link href="https://fonts.googleapis.com/css2?family=Montserrat:wght@400;500;600;800&display=swap" rel="stylesheet">
<style>
  :root {
    --backdrop: #3a3a3c;
    --card-dark: #272526;
    --panel-gray: #5a595b;
    --panel-gray-light: #68676a;
    --tone-helmet: #b58a2c;
    --tone-vest: #b8602a;
    --tone-machine: #a8873a;
    --accent-orange: #f0792b;
    --text-light: #f2f2f2;
    --divider: #6c6a6b;
  }
  * { margin: 0; padding: 0; box-sizing: border-box; }
  html, body { width: 1200px; height: 1015px; overflow: hidden; }
  body {
    background: var(--backdrop);
    font-family: "Montserrat", Arial, sans-serif;
    position: relative;
  }
  .card {
    position: absolute;
    left: 200px;
    width: 800px;
    height: 457px;
    background: var(--card-dark);
    box-shadow: 0 14px 30px rgba(0,0,0,.45);
    overflow: hidden;
  }
  .card--back { top: 33px; }
  .card--front { top: 525px; }

  .panel-art { position: absolute; inset: 0; }

  .brand-name {
    font-family: "Montserrat", Arial, sans-serif;
    font-weight: 800;
    color: var(--accent-orange);
    letter-spacing: 1px;
    white-space: nowrap;
  }
  .card--back .brand-name {
    position: absolute;
    left: 300px;
    top: 198px;
    font-size: 40px;
    transform: rotate(-10deg);
    transform-origin: left center;
  }

  .front-brand {
    position: absolute;
    left: 70px;
    top: 222px;
    display: flex;
    align-items: center;
    gap: 14px;
  }
  .front-brand .brand-dot {
    width: 30px; height: 30px;
    border-radius: 50%;
    background: var(--accent-orange);
  }
  .front-brand .brand-name { font-size: 52px; }

  .divider {
    position: absolute;
    left: 418px;
    top: 100px;
    width: 2px;
    height: 250px;
    background: var(--divider);
  }

  .contact-block {
    position: absolute;
    left: 448px;
    top: 118px;
  }
  .person-name {
    color: var(--accent-orange);
    font-weight: 600;
    font-size: 30px;
    text-transform: uppercase;
    line-height: 1.05;
  }
  .person-role {
    color: var(--text-light);
    font-weight: 500;
    font-size: 22px;
    margin-top: 2px;
  }
  .contact-list { list-style: none; margin-top: 28px; }
  .contact-item {
    display: flex;
    align-items: center;
    gap: 12px;
    color: var(--text-light);
    font-size: 19px;
    height: 36px;
    margin-bottom: 6px;
  }
  .contact-icon {
    width: 32px; height: 32px;
    background: var(--accent-orange);
    display: flex; align-items: center; justify-content: center;
    flex: none;
  }
  .contact-icon svg { width: 20px; height: 20px; }
</style>
</head>
<body>

<section class="card card--back" aria-label="Card back">
  <svg class="panel-art" viewBox="0 0 800 457" width="800" height="457">
    <defs>
      <radialGradient id="workers-tone-a" cx="0.5" cy="0.55" r="0.6">
        <stop offset="0" stop-color="var(--tone-vest)" stop-opacity="0.55"/>
        <stop offset="0.35" stop-color="var(--tone-helmet)" stop-opacity="0.35"/>
        <stop offset="1" stop-color="var(--panel-gray)" stop-opacity="0"/>
      </radialGradient>
      <radialGradient id="workers-tone-b" cx="0.55" cy="0.45" r="0.55">
        <stop offset="0" stop-color="var(--tone-helmet)" stop-opacity="0.5"/>
        <stop offset="0.4" stop-color="var(--tone-vest)" stop-opacity="0.3"/>
        <stop offset="1" stop-color="var(--panel-gray)" stop-opacity="0"/>
      </radialGradient>
      <radialGradient id="machine-tone" cx="0.5" cy="0.5" r="0.6">
        <stop offset="0" stop-color="var(--tone-machine)" stop-opacity="0.75"/>
        <stop offset="0.6" stop-color="#6a6150" stop-opacity="0.5"/>
        <stop offset="1" stop-color="var(--panel-gray)" stop-opacity="0"/>
      </radialGradient>
      <linearGradient id="panel-base" x1="0" y1="0" x2="1" y2="1">
        <stop offset="0" stop-color="var(--panel-gray-light)"/>
        <stop offset="1" stop-color="var(--panel-gray)"/>
      </linearGradient>
    </defs>

    <g role="img" aria-label="Illustration of two cartoon construction workers shaking hands">
      <polygon points="0,0 370,0 370,185 0,250" fill="url(#panel-base)"/>
      <polygon points="0,0 370,0 370,185 0,250" fill="url(#workers-tone-a)"/>
    </g>
    <g role="img" aria-label="Illustration of two cartoon construction workers in hard hats">
      <polygon points="395,0 800,0 800,110 395,181" fill="url(#panel-base)"/>
      <polygon points="395,0 800,0 800,110 395,181" fill="url(#workers-tone-b)"/>
    </g>
    <g role="img" aria-label="Photo of a small yellow excavator">
      <polygon points="0,330 370,265 370,457 0,457" fill="var(--panel-gray)"/>
      <polygon points="0,330 370,265 370,457 0,457" fill="url(#machine-tone)"/>
    </g>
    <g role="img" aria-label="Illustration of two cartoon construction workers standing together">
      <polygon points="395,261 800,190 800,457 395,457" fill="url(#panel-base)"/>
      <polygon points="395,261 800,190 800,457 395,457" fill="url(#workers-tone-a)"/>
    </g>
  </svg>
  <div class="brand-name">FunBrixo</div>
</section>

<section class="card card--front" aria-label="Card front">
  <div class="front-brand">
    <span class="brand-dot"></span>
    <span class="brand-name">FunBrixo</span>
  </div>

  <div class="divider"></div>

  <div class="contact-block">
    <div class="person-name">Carl Dunning</div>
    <div class="person-role">Co-Founder &amp; COO</div>
    <ul class="contact-list">
      <li class="contact-item">
        <span class="contact-icon">
          <svg viewBox="0 0 24 24" fill="#272526"><path d="M6.6 10.8a15.1 15.1 0 0 0 6.6 6.6l2.2-2.2a1 1 0 0 1 1-.25 11.4 11.4 0 0 0 3.6.57 1 1 0 0 1 1 1V20a1 1 0 0 1-1 1A17 17 0 0 1 3 4a1 1 0 0 1 1-1h3.5a1 1 0 0 1 1 1c0 1.25.2 2.45.57 3.57a1 1 0 0 1-.25 1z"/></svg>
        </span>
        (833) 571-FUNBRIX
      </li>
      <li class="contact-item">
        <span class="contact-icon">
          <svg viewBox="0 0 24 24" fill="none" stroke="#272526" stroke-width="2"><rect x="3" y="5" width="18" height="14"/><path d="M3 5l9 8 9-8"/></svg>
        </span>
        Carl@funbrixo-demo.com
      </li>
      <li class="contact-item">
        <span class="contact-icon">
          <svg viewBox="0 0 24 24" fill="none" stroke="#272526" stroke-width="2"><circle cx="12" cy="12" r="9"/><path d="M3 12h18M12 3c3 3 3 15 0 18M12 3c-3 3-3 15 0 18"/></svg>
        </span>
        www.funbrixo-demo.com
      </li>
    </ul>
  </div>
</section>

</body>
</html>
```